Cosmetic oil label design

We need a label for a cosmetic oganic Argan Oil. The oil is organic imported from Morocco, cold pressed without any preservatives. The lable is for our round 30ml Airless Bottle with clear body Matte Gold Cap, Shiny Gold Collar. We want to communicate that our product is organic natural and works for all beauty needs. We want the emphasis on the words No preservatives, additives or perfumes
We have attached a picture of the bottle and our compnay's logo.

the bottle demensions are Width/Front: 33.0mm
Length/Depth: 33.0mm
Height: 115.0mm
Lable demensions: Lenght 4inch, width 1.75inch.

let us know if you need any other information, cheers!
Updates

Target Market(s)

Our target customer is mainly women 16-70, and also men or anyone looking to have healthy skin and hair using natural products

Industry/Entity Type

Product

Requirements
Must have
• Front side must have:
- attached logo
-words: Authentic Moroccan Argan Oil, No preservatives, additives or perfumes,
L’Huile d’Argan, Produit du Maroc, Imported from Morocco, 30ml

Back side
-Ingredients: 100% Pure Argania Spinosa (Argan Oil)
-Directions: Message into skin, hair or desired area until completely absorbed
-Manufactured for and distributed by Velora Traders
482 W 97th street New York , NY 10027
Nice to have
• Would be nice if we can fit the following information in the back of the label

Rich in vitamin E and essential fatty acids,Argan oil has several benefits. It Hydrates and nourishes skin and hair. Can be used for treating dry skin, split ends softening cuticles. It works for all types of skin.

```html
<!DOCTYPE html>
<html lang="en">
<head>
<meta charset="utf-8">
<title>Lumara Moroccan Argan Oil – 30ml Label</title>
<link rel="stylesheet" href="https://fonts.googleapis.com/css2?family=Cinzel:wght@400;500&family=Cormorant+Garamond:wght@500&family=Arimo:wght@400;500&display=swap">
<style>
  :root {
    --cocoa: #231a15;
    --gold-deep: #5a4527;
    --gold-light: #e8b65c;
    --gold-dusk: #6b5a40;
    --gold-text: #e9b861;
    --olive: #8a8232;
  }
  html, body {
    margin: 0;
    padding: 0;
    width: 1200px;
    height: 2743px;
    overflow: hidden;
    background: var(--cocoa);
  }
  .label {
    position: relative;
    width: 1200px;
    height: 2743px;
    overflow: hidden;
  }
  .label-backdrop {
    position: absolute;
    inset: 0;
    display: block;
  }
  .volume {
    position: absolute;
    top: 40px;
    right: 58px;
    margin: 0;
    font-family: "Cormorant Garamond", Georgia, serif;
    font-weight: 500;
    font-size: 76px;
    color: var(--gold-text);
    letter-spacing: 1px;
  }
  .brand-name {
    position: absolute;
    top: 640px;
    left: 0;
    width: 1200px;
    margin: 0;
    text-align: center;
    font-family: "Cinzel", Georgia, serif;
    font-weight: 500;
    font-size: 170px;
    line-height: 1;
    letter-spacing: 12px;
    color: var(--olive);
  }
  .product-title {
    position: absolute;
    top: 1395px;
    left: 0;
    width: 1200px;
    margin: 0;
    text-align: center;
    font-family: "Cinzel", Georgia, serif;
    font-weight: 400;
    font-size: 150px;
    line-height: 172px;
    letter-spacing: 2px;
    color: var(--cocoa);
  }
  .product-title span { display: block; }
  .claims {
    position: absolute;
    top: 2360px;
    left: 0;
    width: 1200px;
    text-align: center;
    font-family: "Arimo", Arial, sans-serif;
    color: var(--gold-text);
  }
  .claims-emphasis {
    margin: 0;
    font-weight: 500;
    font-size: 64px;
    line-height: 70px;
  }
  .claims-origin {
    margin: 26px 0 0;
    font-weight: 400;
    font-size: 54px;
    line-height: 68px;
  }
</style>
</head>
<body>
  <main class="label">
    <svg class="label-backdrop" width="1200" height="2743" viewBox="0 0 1200 2743" aria-hidden="true">
      <defs>
        <linearGradient id="gold-field" x1="0" y1="834" x2="0" y2="2332" gradientUnits="userSpaceOnUse">
          <stop offset="0" stop-color="var(--gold-deep)" stop-opacity="1" style="stop-color:#5a4527"/>
          <stop offset="0.5" style="stop-color:#e8b65c"/>
          <stop offset="1" style="stop-color:#625039"/>
        </linearGradient>
      </defs>
      <rect class="top-band" x="0" y="0" width="1200" height="834" fill="#231a15"/>
      <rect class="gold-field" x="0" y="834" width="1200" height="1498" fill="url(#gold-field)"/>
      <path class="header-curve" d="M10 834 A590 205 0 0 0 1190 834 Z" fill="#231a15"/>
      <rect class="bottom-band" x="0" y="2332" width="1200" height="411" fill="#231a15"/>
    </svg>

    <p class="volume">30ml</p>

    <p class="brand-name">Lumara</p>

    <h1 class="product-title">
      <span>Moroccan</span>
      <span>Argan</span>
      <span>Oil</span>
    </h1>

    <section class="claims">
      <p class="claims-emphasis">No preservatives, additives<br>or parfumes</p>
      <p class="claims-origin">L’Huile d’Argan, Produit du Maroc,<br>Imported from Morocco.</p>
    </section>
  </main>
</body>
</html>
```